wealth management firm, professional group, new model

we have a logo that works but we need a card, white background using our colors...clean look

our tag line if can be used in

The Bridge From Client to Owner

```html
<!DOCTYPE html>
<html lang="en">
<head>
<meta charset="UTF-8">
<title>Verano Wealth Partners – Business Card</title>
<link rel="stylesheet" href="https://fonts.googleapis.com/css2?family=Lato:wght@400;700&display=swap">
<style>
  :root {
    --navy: #14284b;
    --ink: #1d2c4c;
    --muted: #5a5f68;
    --rule: #8a93a3;
    --paper: #ffffff;
    --paper-shade: #ebebeb;
    --backdrop: #e9e6e1;
  }
  * { box-sizing: border-box; margin: 0; padding: 0; }
  html, body {
    width: 1200px; height: 900px; overflow: hidden;
    background: var(--backdrop);
    font-family: "Lato", sans-serif;
  }
  .canvas { position: relative; width: 1200px; height: 900px; }

  .card {
    position: absolute;
    width: 560px; height: 320px;
    border: 9px solid var(--navy);
    background: linear-gradient(110deg, var(--paper-shade) 0%, var(--paper) 75%);
    box-shadow: 0 6px 18px rgba(0,0,0,.18);
  }
  .card--front { left: 110px; top: 100px; }
  .card--back  { left: 530px; top: 480px; }

  .brand {
    display: flex; align-items: center; gap: 10px;
    color: var(--navy); font-weight: 400; font-size: 26px;
    letter-spacing: 0.01em; white-space: nowrap;
  }
  .brand__dot {
    width: 14px; height: 14px; border-radius: 50%;
    background: var(--navy); flex: none;
  }
  .card--front .brand {
    position: absolute; left: 50%; top: 50%;
    transform: translate(-50%, -50%);
  }
  .card--back .brand {
    position: absolute; right: 34px; top: 44px;
    font-size: 20px; gap: 8px;
  }
  .card--back .brand__dot { width: 11px; height: 11px; }

  .contact { position: absolute; left: 40px; bottom: 26px; color: var(--muted); }
  .contact__name {
    color: var(--ink); font-weight: 700; font-size: 17px;
    letter-spacing: 0.02em; text-transform: uppercase;
  }
  .contact__role { font-size: 14px; margin-bottom: 22px; }
  .contact__list { list-style: none; padding-left: 36px; }
  .contact__item {
    display: flex; align-items: center; gap: 8px;
    font-size: 14px; line-height: 1.45;
  }
  .contact__item svg { width: 13px; height: 13px; fill: var(--navy); flex: none; }
  .contact__address {
    margin-left: 36px; margin-top: 6px; padding-top: 6px;
    border-top: 1px solid var(--rule);
    width: 300px; font-size: 14px;
  }
</style>
</head>
<body>
<main class="canvas">

  <section class="card card--front" aria-label="Card front">
    <p class="brand"><span class="brand__dot" aria-hidden="true"></span>Verano Wealth Partners</p>
  </section>

  <section class="card card--back" aria-label="Card back">
    <p class="brand"><span class="brand__dot" aria-hidden="true"></span>Verano Wealth Partners</p>

    <div class="contact">
      <p class="contact__name">Daniel Reyes</p>
      <p class="contact__role">Director</p>
      <ul class="contact__list">
        <li class="contact__item">
          <svg viewBox="0 0 24 24" aria-hidden="true"><path d="M6.6 10.8a15.1 15.1 0 0 0 6.6 6.6l2.2-2.2a1 1 0 0 1 1-.25 11.4 11.4 0 0 0 3.6.57 1 1 0 0 1 1 1V20a1 1 0 0 1-1 1A17 17 0 0 1 3 4a1 1 0 0 1 1-1h3.5a1 1 0 0 1 1 1c0 1.25.2 2.45.57 3.57a1 1 0 0 1-.25 1z"/></svg>
          410-555-0182
        </li>
        <li class="contact__item">
          <svg viewBox="0 0 24 24" aria-hidden="true"><path d="M2 5h20v14H2zm2 2v.2l8 6 8-6V7l-8 6z"/></svg>
          info@veranowealth.com
        </li>
        <li class="contact__item">
          <svg viewBox="0 0 24 24" aria-hidden="true"><path d="M12 2a10 10 0 1 0 0 20 10 10 0 0 0 0-20zm6.9 6h-2.9a15.7 15.7 0 0 0-1.4-3.6A8 8 0 0 1 18.9 8zM12 4a14 14 0 0 1 1.9 4h-3.8A14 14 0 0 1 12 4zM4.3 14a8 8 0 0 1 0-4h3.4a16.5 16.5 0 0 0 0 4zm.8 2h2.9a15.7 15.7 0 0 0 1.4 3.6A8 8 0 0 1 5.1 16zM8 8H5.1a8 8 0 0 1 4.3-3.6A15.7 15.7 0 0 0 8 8zm4 12a14 14 0 0 1-1.9-4h3.8A14 14 0 0 1 12 20zm2.3-6H9.7a14.7 14.7 0 0 1 0-4h4.6a14.7 14.7 0 0 1 0 4zm.3 5.6a15.7 15.7 0 0 0 1.4-3.6h2.9a8 8 0 0 1-4.3 3.6zm1.7-5.6a16.5 16.5 0 0 0 0-4h3.4a8 8 0 0 1 0 4z"/></svg>
          www.veranowealth.com
        </li>
      </ul>
      <p class="contact__address">00 dummy city, dummy place 0000</p>
    </div>
  </section>

</main>
</body>
</html>
```